Design a modern, classy & professional business card for an online real estate agency, specializing in medium-luxury properties in Thailand and later in Singapore and UK.

Possible design ideas so far: (not essential)

- curved corner(s) to the card, white on front & turquoise on back or visa versa.

- front of card - clear and simple, company name in metallic grey/monochrome, logo graphic & company name on front in spot UV or embossed/debossed effect.

- back of card - large, close-cropped, 'ghost' patterns of the C-shaped curves of logo, or company name repeated on back of card in spot UV.

Target Market(s)

- young to middle-aged professionals mainly (but ideally should design should suit all)

- UK, US,EU,AUS & ASIAN mainly (but ideally should design should suit all countries)

Industry/Entity Type

Real Estate

Requirements
Must have
• THEME:
- Luxurious & Modern
- Clean & striking
- Unique & creative

INFO:
- Logo & company name on front
- Contact details on back:

Tobias Hennlund
Managing Director

www.velmontestates.asia
www.velmontestates.co.uk

Tel: 083-274-6159
email: tobias@velmontestates.asia

(contact details can be displayed in any order as suites design.)

Nice to have
• - curved corner(s) to the card, white on front & turquoise on back or visa versa.

Should not have
• - No generic images of properties, palm trees/coconut trees etc.

- No other other bold colors, except for main turquoise, grey, metallic white & black theme.

- No obvious business card templates

```html
<!DOCTYPE html>
<html lang="en">
<head>
<meta charset="utf-8">
<title>Velmont Estates – Business Card</title>
<link rel="stylesheet" href="https://fonts.googleapis.com/css2?family=Cormorant+Garamond:wght@500&family=Arimo:wght@400;700&display=swap">
<style>
  :root {
    --backdrop: #e9eaea;
    --card-white: #ffffff;
    --ghost-light: #f7f8f8;
    --ghost-mid: #eceeee;
    --turquoise: #5bb8b3;
    --turquoise-light: #9fd9d5;
    --grey-metal: #8a8c8e;
    --ink: #1e1e1e;
    --swoosh-black: #2a2a2a;
  }
  * { box-sizing: border-box; margin: 0; padding: 0; }
  html, body { width: 1200px; height: 913px; overflow: hidden; }
  body {
    background: var(--backdrop);
    position: relative;
    font-family: "Arimo", Arial, sans-serif;
  }
  .card {
    position: absolute;
    width: 540px;
    height: 309px;
    border-radius: 22px;
    background: var(--card-white);
    overflow: hidden;
    box-shadow: 0 6px 18px rgba(0,0,0,0.12);
  }
  .card--front { left: 40px; top: 302px; }
  .card--back  { left: 620px; top: 302px; }

  .ghost-pattern {
    position: absolute; inset: 0;
    background: radial-gradient(ellipse at 50% 50%, var(--ghost-light) 0%, var(--ghost-mid) 100%);
  }

  .brand {
    position: absolute;
    display: flex;
    align-items: center;
    gap: 16px;
  }
  .brand__mark {
    background: var(--turquoise);
    flex: none;
  }
  .brand__name {
    font-family: "Cormorant Garamond", Georgia, serif;
    font-weight: 500;
    color: var(--grey-metal);
    white-space: nowrap;
    letter-spacing: 0.5px;
  }
  .card--front .brand { left: 92px; top: 118px; }
  .card--front .brand__mark { width: 76px; height: 76px; }
  .card--front .brand__name { font-size: 50px; }

  .card--back .brand { left: 30px; top: 62px; gap: 14px; }
  .card--back .brand__mark { width: 60px; height: 60px; }
  .card--back .brand__name { font-size: 34px; }

  .swoosh { position: absolute; inset: 0; width: 540px; height: 309px; }

  .contact {
    position: absolute;
    left: 36px;
    top: 150px;
    list-style: none;
  }
  .contact__item {
    display: flex;
    align-items: center;
    gap: 10px;
    font-size: 13px;
    font-weight: 700;
    color: var(--ink);
    height: 21px;
  }
  .contact__icon { width: 14px; height: 14px; flex: none; }

  .person {
    position: absolute;
    right: 22px;
    top: 116px;
    text-align: right;
    color: var(--card-white);
    white-space: nowrap;
  }
  .person__name { font-size: 15px; font-weight: 700; }
  .person__title { font-size: 11px; font-weight: 400; margin-top: 4px; }
</style>
</head>
<body>

  <section class="card card--front">
    <div class="ghost-pattern" role="img" aria-label="Faint spot-UV pattern of interlocking circles across the card"></div>
    <div class="brand">
      <span class="brand__mark"></span>
      <span class="brand__name">Velmont Estates</span>
    </div>
  </section>

  <section class="card card--back">
    <svg class="swoosh" viewBox="0 0 540 309" aria-hidden="true">
      <defs>
        <linearGradient id="teal-fade" x1="0" y1="0" x2="0" y2="1">
          <stop offset="0" stop-color="var(--turquoise-light)"/>
          <stop offset="1" stop-color="var(--turquoise)"/>
        </linearGradient>
      </defs>
      <path d="M200 309 C300 280 340 200 365 125 C390 55 440 20 540 6 L540 309 Z" fill="url(#teal-fade)"/>
      <path d="M0 292 C140 304 280 294 335 205 C360 160 380 70 470 12" fill="none" stroke="var(--grey-metal)" stroke-width="9" stroke-linecap="round"/>
      <path d="M0 303 C150 310 295 302 350 212 C375 170 395 85 490 20" fill="none" stroke="var(--swoosh-black)" stroke-width="5" stroke-linecap="round"/>
      <path d="M0 309 L0 300 C60 306 120 309 160 309 Z" fill="var(--turquoise)"/>
    </svg>

    <div class="brand">
      <span class="brand__mark"></span>
      <span class="brand__name">Velmont Estates</span>
    </div>

    <ul class="contact">
      <li class="contact__item">
        <svg class="contact__icon" viewBox="0 0 16 16" aria-hidden="true"><path d="M2 5 C2 3 5 2 8 2 C11 2 14 3 14 5 L12 6 L10 5 L10 4 H6 V5 L4 6 Z M4 8 H12 L13 14 H3 Z" fill="var(--turquoise)"/></svg>
        083-274-6159
      </li>
      <li class="contact__item">
        <svg class="contact__icon" viewBox="0 0 16 16" aria-hidden="true"><rect x="1" y="3" width="14" height="10" fill="var(--turquoise)"/><path d="M1 3 L8 9 L15 3" fill="none" stroke="#fff" stroke-width="1.4"/></svg>
        tobias@velmontestates.asia
      </li>
      <li class="contact__item">
        <svg class="contact__icon" viewBox="0 0 16 16" aria-hidden="true"><circle cx="8" cy="8" r="7" fill="var(--turquoise)"/><path d="M1 8 H15 M8 1 C4 5 4 11 8 15 M8 1 C12 5 12 11 8 15" fill="none" stroke="#fff" stroke-width="1"/></svg>
        www.velmontestates.asia
      </li>
      <li class="contact__item">
        <span class="contact__icon"></span>
        www.velmontestates.co.uk
      </li>
    </ul>

    <div class="person">
      <p class="person__name">Tobias Hennlund</p>
      <p class="person__title">Managing Director</p>
    </div>
  </section>

</body>
</html>
```